Norva Skills Brochure Design Project

Our company requires a brochure for promoting our Corporate Training business.

Please use data from Corporate training brochure doc.
Updates

Dear Designers,

We have added new corporate brochure document into the project. Use this data to finish up your brochure.

Thanks,

Rena voskov

Reason: We have recently finalised the data that will go into the corporate brochure.

Reason: To get more better designs

Target Market(s)

Training Managers / Business Managers / Hiring Managers

Industry/Entity Type

Training

Requirements
Must have
• Corporate and Professional Look

```html
<!DOCTYPE html>
<html lang="en">
<head>
<meta charset="utf-8">
<title>Norva Skills – Corporate Customised IT Training Brochure</title>
<link rel="stylesheet" href="https://fonts.googleapis.com/css2?family=Source+Sans+3:wght@400;600&family=PT+Sans+Narrow:wght@400;700&display=swap">
<style>
  :root {
    --slate: #5a5b5d;
    --ink: #000000;
    --paper: #ffffff;
    --gold-1: #f2a516;
    --gold-2: #f7c62a;
    --gold-3: #f3e56a;
    --step-yellow: #fff200;
    --photo-office: #8c8f86;
    --photo-server: #b9bec4;
    --photo-portrait: #6b5a52;
    --swoosh-light: #c9c9c2;
    --swoosh-dark: #3f4042;
  }
  * { margin: 0; padding: 0; box-sizing: border-box; }
  html, body { width: 1200px; height: 848px; overflow: hidden; background: var(--slate); }
  .spread {
    position: relative; width: 1200px; height: 848px; overflow: hidden;
    background: var(--slate); color: var(--paper);
    font-family: "Source Sans 3", "Segoe UI", sans-serif;
  }
  .block { position: absolute; background: var(--ink); }
  .gold-band {
    position: absolute; top: 82px; height: 27px;
    background: linear-gradient(90deg, var(--gold-1), var(--gold-2) 50%, var(--gold-3));
  }
  .photo { position: absolute; }
  .photo-office { left: 24px; top: 100px; width: 349px; height: 202px;
    background: linear-gradient(135deg, #b7b9b1, var(--photo-office) 45%, #4f5a3f); }
  .photo-server { left: 373px; top: 406px; width: 224px; height: 352px;
    background: linear-gradient(90deg, #6d747c, var(--photo-server) 50%, #e8ecef); }
  .photo-portrait { left: 940px; top: 179px; width: 234px; height: 370px;
    background: linear-gradient(160deg, #2f3338, var(--photo-portrait) 55%, #1c1d20); }
  .swoosh { position: absolute; right: 0; top: 0; width: 130px; height: 848px; }
  .wordmark { font-weight: 600; letter-spacing: -1px; line-height: 1; color: var(--paper); }
  .panel-left { position: absolute; left: 66px; top: 326px; width: 262px; }
  .panel-left .wordmark { font-size: 50px; }
  .tagline { font-size: 15px; margin-top: 6px; }
  .copy { font-size: 9.6px; line-height: 16px; }
  .copy p { margin-bottom: 16px; }
  .intro { margin-top: 12px; }
  .intro p { margin-bottom: 8px; }
  .section-title { font-size: 22px; font-weight: 400; margin: 14px 0 2px; }
  .panel-right { position: absolute; left: 661px; top: 176px; width: 244px; }
  .panel-right .wordmark { font-size: 44px; }
  .panel-right .tagline { font-size: 13.5px; margin: 8px 0 14px; }
  .note { font-size: 7px; line-height: 15px; margin-top: -4px; }
  .steps { position: absolute; left: 0; top: 0; width: 1200px; height: 848px; }
  .step-label, .step-text {
    position: absolute; font-family: "PT Sans Narrow", "Arial Narrow", sans-serif; white-space: nowrap;
  }
  .step-label { font-size: 10px; font-weight: 700; }
  .step-text { font-size: 9.5px; }
</style>
</head>
<body>
<main class="spread">
  <div class="block" style="left:24px;top:0;width:349px;height:102px"></div>
  <div class="block" style="left:373px;top:300px;width:224px;height:548px"></div>
  <div class="block" style="left:940px;top:549px;width:234px;height:180px"></div>

  <div class="gold-band" style="left:0;width:52px"></div>
  <div class="gold-band" style="left:346px;width:800px"></div>

  <div class="photo photo-office" role="img" aria-label="Photo of a businesswoman seated in an office courtyard beside plants"></div>
  <div class="photo photo-server" role="img" aria-label="Photo of an IT technician working on a laptop in a server room"></div>
  <div class="photo photo-portrait" role="img" aria-label="Photo of smiling businesswomen in an office"></div>

  <svg class="swoosh" viewBox="0 0 130 848" aria-hidden="true">
    <defs>
      <linearGradient id="swoosh-fill" x1="0" y1="0" x2="1" y2="0">
        <stop offset="0" stop-color="var(--swoosh-light)"/>
        <stop offset="1" stop-color="var(--swoosh-dark)"/>
      </linearGradient>
    </defs>
    <path d="M70 0 C120 150 110 300 70 430 C40 560 60 720 40 848 L130 848 L130 0 Z" fill="url(#swoosh-fill)"/>
    <path d="M70 0 C120 150 110 300 70 430 C40 560 60 720 40 848" fill="none" stroke="#e6e6e0" stroke-width="2"/>
  </svg>

  <section class="panel-left">
    <h1 class="wordmark">Norva Skills</h1>
    <p class="tagline">Corporate Customised IT Training</p>
    <div class="copy intro">
      <p>Get a Training Program as exclusive as your business needs<br>Love our training or your money back!</p>
      <p>If you could improve your business would you?</p>
    </div>
    <h2 class="section-title">About US</h2>
    <div class="copy">
      <p>Norva Skills is firmly positioned as one of the most successful IT Training provider throughout Australia. With highly qualified, cross vendor-certified instructors having proficiency, extensive hands-on-experience and technical expertise, Norva Skills ensure that it provides excellent quality training suitable to its clients needs.</p>
      <p>Norva Skills work individually with companies to understand their vision and identify their learning needs and objectives. We specialise in designing programs to meet the specific content, location and scheduling requirements of your organisation. By continuing to meet the evolving needs of our clients, the number of people choosing Norva Skills is growing every year.</p>
      <p>If you could improve your Staff performance would you?</p>
    </div>
  </section>

  <section class="panel-right">
    <h2 class="wordmark">Norva Skills</h2>
    <p class="tagline">Our Customised Training</p>
    <div class="copy">
      <p>Instead of sending your staff to attend external public training programs, there is more cost effective way of enhancing work performance and updating professional skills.</p>
      <p>You can choose from our broad range of programs across different levels from servers to networks and everything revolving around it which can then be customised to suit. By having a program tailored to the individual needs of your business, your staff will benefit from using scenarios and examples that are relevant to your specific organisation. This ensures that skills gained through our training program can be effectively applied to your work place.</p>
      <p>We commence by assessing your needs. Our consultant works with you to understand your business goals and develop a training plan exclusive for your organisation.</p>
    </div>
    <p class="note">(The following model is taken from Kestrel Labs website. Needs to be changed in a different format, look and wording.)</p>
  </section>

  <svg class="steps" viewBox="0 0 1200 848" aria-hidden="true">
    <polyline fill="none" stroke="var(--step-yellow)" stroke-width="5"
      points="666,717 721,717 721,692 776,692 776,667 831,667 831,642 886,642 886,617 942,617 942,593 1089,593"/>
  </svg>
  <span class="step-label" style="left:677px;top:694px">ASSESS</span>
  <span class="step-label" style="left:732px;top:669px">DESIGN</span>
  <span class="step-label" style="left:783px;top:645px">DEVELOP</span>
  <span class="step-label" style="left:838px;top:620px">DELIVER</span>
  <span class="step-label" style="left:891px;top:596px">MAINTAIN</span>
  <span class="step-text" style="left:730px;top:702px">Understand Your Learning Issues</span>
  <span class="step-text" style="left:790px;top:677px">Design Your Training Solution</span>
  <span class="step-text" style="left:845px;top:653px">Develop Your Course Content</span>
  <span class="step-text" style="left:893px;top:629px">Deliver Your Training</span>
  <span class="step-text" style="left:949px;top:605px">Provide-Ongoing Training Support</span>
</main>
</body>
</html>
```